Seed Oil Safety Card for Healthy Restaurant Dining

I am seeking a design for a physical card to communicate my wife's health-related dietary restriction regarding seed oils. This card will be given to restaurant waiters to ensure her meals are prepared without seed oils, as it is a health issue and not merely a preference.
My wife cannot eat any “seed oil” or “processed oil”, including:
- Vegetable oil
- Canola oil
- Soybean oil
- Sunflower oil
- Corn oil
- Cottonseed oil
- Safflower oil
- Peanut oil
- Sesame oil
Oils that are OK for her to consume:
- Butter (most preferable)
- Extra virgin olive oil
- Avocado oil
- Coconut oil
- Ghee
- Lard
- Any other animal-based fats
Key Design Requirements:
- Clarity and speed of communication: The card should be easily read and understood by waiters, even in low-light environments, emphasizing that it's a health concern.
- Avoid common misconceptions: Ensure the design doesn't imply common dietary preferences like "vegetarian" or "no butter." Animal fats and butter are actually preferable for her!
- Preferred term: Use "seed oils" as the term to describe what she cannot eat due to her health issue.
- Trace amounts are acceptable: Communicate that it's OK to use cookware that has previously been in contact with seed oils, but not to have seed oil as an ingredient. Please suggest a concise way to convey this.
- Card dimensions: Design should be 3.5” x 2.25” (standard credit-card size on printorvale.example). Horizontal or vertical layouts are both fine, whichever makes the message clearer.
Design Suggestions:
- Utilize bold and easy-to-read typography to communicate the main message.
- Consider incorporating relevant icons or graphics that help convey the message without adding confusion.
- Use contrasting colors to enhance readability, especially in low-light situations.
- To communicate the “trace amounts OK” part, consider phrases such as:
- "Cross-contamination acceptable"
- “Used cookware OK, no ingredient use”
- “Separate cookware not necessary”
Thank you for your assistance in creating this essential card for my wife's health and safety when dining out!

```html
<!DOCTYPE html>
<html lang="en">
<head>
<meta charset="utf-8">
<title>Seed Oil Allergy Card</title>
<link href="https://fonts.googleapis.com/css2?family=Roboto+Condensed:ital,wght@0,700;1,500&display=swap" rel="stylesheet">
<style>
  :root {
    --backdrop: #999999;
    --card: #ffffff;
    --ink: #0b0b0b;
    --avoid: #94202a;
    --safe: #17703a;
  }
  * { margin: 0; padding: 0; box-sizing: border-box; }
  html, body { width: 1200px; height: 1200px; overflow: hidden; background: var(--backdrop); }
  body { position: relative; font-family: "Roboto Condensed", "Arial Narrow", sans-serif; font-weight: 700; }
  .card {
    position: absolute; left: 302px; top: 138px; width: 595px; height: 924px;
    background: var(--card); border-radius: 38px;
  }
  .title {
    position: absolute; left: 0; width: 100%; top: 30px; text-align: center;
    font-size: 62px; letter-spacing: 1.5px; color: var(--ink); line-height: 1;
  }
  .title-rule {
    position: absolute; left: 159px; top: 108px; width: 277px; height: 5px; background: var(--ink);
  }
  .column { position: absolute; top: 0; width: 250px; }
  .column--avoid { left: 28px; }
  .column--safe { left: 298px; }
  .column-icon { position: absolute; top: 165px; left: 89px; width: 74px; height: 74px; }
  .column-heading {
    position: absolute; top: 255px; left: -20px; width: 290px; text-align: center;
    font-size: 39px; line-height: 33px; letter-spacing: 1.2px; color: var(--ink); white-space: nowrap;
  }
  .column-pointer { position: absolute; top: 341px; left: 103px; width: 45px; height: 25px; }
  .item-list { position: absolute; list-style: none; font-size: 30px; line-height: 37px; letter-spacing: 0.5px; }
  .column--avoid .item-list { top: 378px; left: 16px; color: var(--avoid); }
  .column--safe .item-list { top: 381px; left: -6px; color: var(--safe); }
  .item-list li { position: relative; padding-left: 30px; white-space: nowrap; }
  .item-list svg { position: absolute; left: 0; top: 11px; width: 17px; height: 17px; }
  .note {
    position: absolute; left: 0; width: 100%; top: 800px; text-align: center;
    font-style: italic; font-weight: 500; font-size: 26px; line-height: 30px;
    letter-spacing: 1.2px; color: var(--ink); white-space: nowrap;
  }
</style>
</head>
<body>
  <div class="card">
    <h1 class="title">SEED OIL ALLERGY!</h1>
    <div class="title-rule"></div>

    <section class="column column--avoid">
      <svg class="column-icon" viewBox="0 0 74 74" aria-hidden="true">
        <rect x="2.5" y="2.5" width="69" height="69" rx="3" fill="none" stroke="var(--avoid)" stroke-width="4"/>
        <path d="M19 19 L55 55 M55 19 L19 55" stroke="var(--avoid)" stroke-width="11"/>
      </svg>
      <h2 class="column-heading">Cannot<br>Consume</h2>
      <svg class="column-pointer" viewBox="0 0 45 25" aria-hidden="true"><path d="M0 0 H45 L22.5 25 Z" fill="var(--ink)"/></svg>
      <ul class="item-list">
        <li><svg viewBox="0 0 17 17"><rect x="1" y="1" width="15" height="15" fill="none" stroke="currentColor" stroke-width="1.6"/><path d="M5 5 L12 12 M12 5 L5 12" stroke="currentColor" stroke-width="2"/></svg>Vegetable oil</li>
        <li><svg viewBox="0 0 17 17"><rect x="1" y="1" width="15" height="15" fill="none" stroke="currentColor" stroke-width="1.6"/><path d="M5 5 L12 12 M12 5 L5 12" stroke="currentColor" stroke-width="2"/></svg>Canola oil</li>
        <li><svg viewBox="0 0 17 17"><rect x="1" y="1" width="15" height="15" fill="none" stroke="currentColor" stroke-width="1.6"/><path d="M5 5 L12 12 M12 5 L5 12" stroke="currentColor" stroke-width="2"/></svg>Soybean oil</li>
        <li><svg viewBox="0 0 17 17"><rect x="1" y="1" width="15" height="15" fill="none" stroke="currentColor" stroke-width="1.6"/><path d="M5 5 L12 12 M12 5 L5 12" stroke="currentColor" stroke-width="2"/></svg>Sunflower oil</li>
        <li><svg viewBox="0 0 17 17"><rect x="1" y="1" width="15" height="15" fill="none" stroke="currentColor" stroke-width="1.6"/><path d="M5 5 L12 12 M12 5 L5 12" stroke="currentColor" stroke-width="2"/></svg>Corn oil</li>
        <li><svg viewBox="0 0 17 17"><rect x="1" y="1" width="15" height="15" fill="none" stroke="currentColor" stroke-width="1.6"/><path d="M5 5 L12 12 M12 5 L5 12" stroke="currentColor" stroke-width="2"/></svg>Cottonseed oil</li>
        <li><svg viewBox="0 0 17 17"><rect x="1" y="1" width="15" height="15" fill="none" stroke="currentColor" stroke-width="1.6"/><path d="M5 5 L12 12 M12 5 L5 12" stroke="currentColor" stroke-width="2"/></svg>Safflower oil</li>
        <li><svg viewBox="0 0 17 17"><rect x="1" y="1" width="15" height="15" fill="none" stroke="currentColor" stroke-width="1.6"/><path d="M5 5 L12 12 M12 5 L5 12" stroke="currentColor" stroke-width="2"/></svg>Peanut oil</li>
        <li><svg viewBox="0 0 17 17"><rect x="1" y="1" width="15" height="15" fill="none" stroke="currentColor" stroke-width="1.6"/><path d="M5 5 L12 12 M12 5 L5 12" stroke="currentColor" stroke-width="2"/></svg>Sesame oil</li>
      </ul>
    </section>

    <section class="column column--safe">
      <svg class="column-icon" viewBox="0 0 74 74" aria-hidden="true">
        <rect x="2.5" y="2.5" width="69" height="69" rx="3" fill="none" stroke="var(--safe)" stroke-width="4"/>
        <path d="M17 38 L30 51 L57 22" fill="none" stroke="var(--safe)" stroke-width="10"/>
      </svg>
      <h2 class="column-heading">OK<br>To Consume</h2>
      <svg class="column-pointer" viewBox="0 0 45 25" aria-hidden="true"><path d="M0 0 H45 L22.5 25 Z" fill="var(--ink)"/></svg>
      <ul class="item-list">
        <li><svg viewBox="0 0 17 17"><rect x="1" y="1" width="15" height="15" fill="none" stroke="currentColor" stroke-width="1.6"/><path d="M4.5 9 L7.5 12 L12.5 5" fill="none" stroke="currentColor" stroke-width="2"/></svg>Butter<br>(most preferable)</li>
        <li><svg viewBox="0 0 17 17"><rect x="1" y="1" width="15" height="15" fill="none" stroke="currentColor" stroke-width="1.6"/><path d="M4.5 9 L7.5 12 L12.5 5" fill="none" stroke="currentColor" stroke-width="2"/></svg>Extra virgin</li>
        <li><svg viewBox="0 0 17 17"><rect x="1" y="1" width="15" height="15" fill="none" stroke="currentColor" stroke-width="1.6"/><path d="M4.5 9 L7.5 12 L12.5 5" fill="none" stroke="currentColor" stroke-width="2"/></svg>Olive oil</li>
        <li><svg viewBox="0 0 17 17"><rect x="1" y="1" width="15" height="15" fill="none" stroke="currentColor" stroke-width="1.6"/><path d="M4.5 9 L7.5 12 L12.5 5" fill="none" stroke="currentColor" stroke-width="2"/></svg>Avocado oil</li>
        <li><svg viewBox="0 0 17 17"><rect x="1" y="1" width="15" height="15" fill="none" stroke="currentColor" stroke-width="1.6"/><path d="M4.5 9 L7.5 12 L12.5 5" fill="none" stroke="currentColor" stroke-width="2"/></svg>Coconut oil</li>
        <li><svg viewBox="0 0 17 17"><rect x="1" y="1" width="15" height="15" fill="none" stroke="currentColor" stroke-width="1.6"/><path d="M4.5 9 L7.5 12 L12.5 5" fill="none" stroke="currentColor" stroke-width="2"/></svg>Ghee</li>
        <li><svg viewBox="0 0 17 17"><rect x="1" y="1" width="15" height="15" fill="none" stroke="currentColor" stroke-width="1.6"/><path d="M4.5 9 L7.5 12 L12.5 5" fill="none" stroke="currentColor" stroke-width="2"/></svg>Lard</li>
        <li><svg viewBox="0 0 17 17"><rect x="1" y="1" width="15" height="15" fill="none" stroke="currentColor" stroke-width="1.6"/><path d="M4.5 9 L7.5 12 L12.5 5" fill="none" stroke="currentColor" stroke-width="2"/></svg>Any other<br>animal-based fats</li>
      </ul>
    </section>

    <p class="note">"Cross-contamination acceptable"<br>“Used cookware OK, no ingredient use”<br>“Separate cookware not necessary”</p>
  </div>
</body>
</html>
```